Hollendorf Business Card

This is the personal business card for Dr Mark Hollendorf and convers three area of his professional activity - all of them involve (foreign) languages:
o QRVB International Ltd - A translation company with 50 staff. Trades internationally
o WideHarbor Ltd - a global online auction marketplace for translation services (startup)
o Tonal Mosaic - cutting edge technology from the brain sciences which helps learners assimilate the sound patterns of a new language (startup)

Target Market(s)

The card needs to have a "cutting edge" feel - but for a fairly conservative audience - academics, investors.

Industry/Entity Type

Business

Requirements
Must have
• Text:
Dr Mark Hollendorf

Co-founder QRVB International Ltd (Language translation)
Founder WideHarbor Ltd (Translation marketplace)
Founder Tonal Mosaic (Language acquisition)

email: mark.oswin@velmora.co.nz
Phone: +64 21 596 3172
Twitter: @MarkOswin7

```html
<!DOCTYPE html>
<html lang="en">
<head>
<meta charset="utf-8">
<title>Dr Mark Hollendorf – Business Card</title>
<link rel="stylesheet" href="https://fonts.googleapis.com/css2?family=Libre+Franklin:wght@600;700&family=Arimo:wght@400&family=Roboto:wght@300;400&display=swap">
<style>
  :root {
    --paper: #ffffff;
    --ink: #1a1a1a;
    --ink-soft: #333333;
    --gold: #c99a1c;
    --ring: #d4a935;
    --band-start: #c9c9a3;
    --band-end: #f1f1e4;
  }
  * { margin: 0; padding: 0; box-sizing: border-box; }
  html, body {
    width: 1200px;
    height: 686px;
    overflow: hidden;
    background: var(--paper);
  }
  .card {
    position: relative;
    width: 1200px;
    height: 686px;
    background: var(--paper);
    color: var(--ink);
    overflow: hidden;
  }
  .card__graphics {
    position: absolute;
    inset: 0;
  }
  .card__side-name {
    position: absolute;
    left: 112px;
    top: 636px;
    transform-origin: 0 0;
    transform: rotate(-90deg) translateY(-50%);
    font-family: "Libre Franklin", Arial, sans-serif;
    font-weight: 700;
    font-size: 29px;
    letter-spacing: 0.3em;
    white-space: nowrap;
    color: var(--ink);
  }
  .card__name {
    position: absolute;
    left: 270px;
    top: 218px;
    font-family: "Libre Franklin", Arial, sans-serif;
    font-weight: 700;
    font-size: 34px;
    letter-spacing: 0.12em;
    white-space: nowrap;
    color: var(--ink);
  }
  .card__tagline {
    position: absolute;
    left: 583px;
    top: 306px;
    width: 545px;
    font-family: "Libre Franklin", Arial, sans-serif;
    font-weight: 700;
    font-size: 24px;
    line-height: 34px;
    letter-spacing: 0.2em;
    text-align: center;
    color: var(--ink);
  }
  .ventures {
    position: absolute;
    left: 199px;
    top: 392px;
    list-style: none;
    font-family: "Arimo", Verdana, sans-serif;
    font-size: 18.5px;
    line-height: 38px;
    color: var(--ink);
  }
  .ventures__item + .ventures__item { margin-top: 14px; }
  .ventures__role, .ventures__field { display: block; }
  .contact {
    position: absolute;
    left: 716px;
    top: 414px;
    font-family: "Roboto", Arial, sans-serif;
    font-weight: 400;
    font-size: 27px;
    line-height: 48px;
    color: var(--ink-soft);
    list-style: none;
  }
</style>
</head>
<body>
<main class="card">
  <svg class="card__graphics" width="1200" height="686" viewBox="0 0 1200 686" aria-hidden="true">
    <defs>
      <linearGradient id="band-fade" x1="0" y1="0" x2="1" y2="0">
        <stop offset="0" stop-color="var(--band-start)" style="stop-color: var(--band-start)"/>
        <stop offset="1" stop-color="var(--band-end)" style="stop-color: var(--band-end)"/>
      </linearGradient>
    </defs>
    <rect class="band" x="200" y="206" width="925" height="71" fill="url(#band-fade)"/>
    <circle class="ring" cx="525" cy="330" r="284" fill="none" stroke="var(--ring)" stroke-width="2.5" style="stroke: var(--ring)"/>
    <path class="bracket bracket--left" d="M228 166 H209 V318 H228" fill="none" stroke="var(--ink)" stroke-width="10" style="stroke: var(--ink)"/>
    <path class="bracket bracket--right" d="M1124 110 H1148 V268 H1124" fill="none" stroke="var(--gold)" stroke-width="9" style="stroke: var(--gold)"/>
  </svg>

  <div class="card__side-name">DR. MARK HOLLENDORF</div>

  <h1 class="card__name">MARK HOLLENDORF</h1>
  <p class="card__tagline">PROFESSION IN FOREIGN<br>LANGUAGES</p>

  <ul class="ventures">
    <li class="ventures__item">
      <span class="ventures__role">Co-founder QRVB International Ltd</span>
      <span class="ventures__field">(Language Translation)</span>
    </li>
    <li class="ventures__item">
      <span class="ventures__role">Founder WideHarbor Ltd</span>
      <span class="ventures__field">(Translation Marketplace)</span>
    </li>
    <li class="ventures__item">
      <span class="ventures__role">Founder Tonal Mosaic</span>
      <span class="ventures__field">(Language Acquisition)</span>
    </li>
  </ul>

  <ul class="contact">
    <li class="contact__phone">Phone: +64 21 596 3172</li>
    <li class="contact__twitter">Twitter: @MarkOswin7</li>
    <li class="contact__email">E-mail: mark.oswin@velmora.co.nz</li>
  </ul>
</main>
</body>
</html>
```